Jolly Paws Business Card Update

I have a business card which I love. I want to keep the same logo, colours, font and style. I want to upgrade the scripting and remove some elements and add others.
On the front side under Services - remove the existing wording and insert - Providing individual coaching strategies to create happy, healthy and social canine companions
Under Denise Carvell amend the current wording to read: Qualified in Dog Behavioural Training, Natural Animal Healthcare and Animal Health Science
On the reverse side to remove the web address.

```html
<!DOCTYPE html>
<html lang="en">
<head>
<meta charset="utf-8">
<title>Jolly Paws Business Card</title>
<link rel="stylesheet" href="https://fonts.googleapis.com/css2?family=Arimo:wght@400;700&family=Oxygen:wght@400;700&display=swap">
<style>
  :root {
    --backdrop: #2c2c2c;
    --blue-deep: #23408e;
    --blue-mid: #1b5aa6;
    --blue-bright: #0b8fcd;
    --red-dark: #6e1a1a;
    --red-bright: #d41c22;
    --emblem-red: #c81d22;
    --paper: #f2f2f2;
    --navy-text: #25317e;
    --ink: #111;
    --white: #fff;
  }
  * { margin: 0; padding: 0; box-sizing: border-box; }
  html, body { width: 1200px; height: 1138px; overflow: hidden; }
  body { background: var(--backdrop); position: relative; font-family: "Arimo", Arial, sans-serif; }

  .card {
    position: absolute; left: 275px; width: 620px; height: 375px;
    border-radius: 14px; overflow: hidden;
    box-shadow: 0 4px 10px rgba(0,0,0,.45);
  }
  .card--front { top: 186px; background: linear-gradient(200deg, var(--blue-bright) 0%, var(--blue-mid) 45%, var(--blue-deep) 100%); }
  .card--back { top: 608px; background: var(--paper); }

  .brand-name {
    position: absolute; left: 34px; top: 54px;
    font-family: "Arimo", Arial, sans-serif; font-weight: 400; font-size: 33px; line-height: 36px;
    color: var(--white); letter-spacing: 1px;
  }
  .brand-tagline {
    position: absolute; left: 34px; top: 92px;
    font-size: 17px; color: var(--white); letter-spacing: .3px;
  }
  .services { position: absolute; color: var(--white); }
  .services h2 { font-size: 17px; font-weight: 700; line-height: 20px; }
  .services p { font-size: 16px; line-height: 19px; }
  .card--front .services { left: 36px; top: 182px; width: 240px; }

  .band-red { position: absolute; left: 0; right: 0;
    background: linear-gradient(90deg, var(--red-dark) 0%, var(--red-bright) 55%, var(--red-dark) 100%); }
  .card--front .band-red { top: 324px; bottom: 0; }
  .band-red .motto { display: block; text-align: center; color: var(--white); font-size: 16px; line-height: 51px; }

  .emblem { position: absolute; }
  .emblem svg { display: block; }

  .person-name { position: absolute; left: 22px; top: 38px; font-family: "Oxygen", Arial, sans-serif; font-weight: 700; font-size: 25px; color: var(--navy-text); }
  .qualifications { position: absolute; left: 22px; top: 70px; font-family: "Oxygen", Arial, sans-serif; font-size: 14px; line-height: 20px; color: var(--navy-text); }

  .card--back .band-red { top: 136px; height: 66px; }
  .contact { position: absolute; left: 22px; top: 157px; font-family: "Oxygen", Arial, sans-serif; font-size: 15.5px; color: var(--white); }
  .contact-row { display: flex; align-items: center; height: 23px; }
  .contact-row svg { margin-right: 9px; }
  .contact-row .gap { width: 12px; }

  .band-blue { position: absolute; left: 0; right: 0; top: 202px; height: 102px;
    background: linear-gradient(90deg, var(--blue-deep) 0%, var(--blue-mid) 55%, var(--blue-bright) 100%); }
  .card--back .services { left: 22px; top: 222px; width: 345px; }
  .card--back .services h2 { font-size: 18px; line-height: 24px; }
  .card--back .services p { font-size: 15.5px; line-height: 18px; }
  .footer-motto { position: absolute; left: 22px; top: 338px; font-size: 16px; color: var(--ink); }
</style>
</head>
<body>

<section class="card card--front" aria-label="Card front">
  <h1 class="brand-name">JOLLY PAWS</h1>
  <p class="brand-tagline">HAPPY DOGS, HAPPY OWNERS</p>
  <div class="services">
    <h2>SERVICES</h2>
    <p>Providing individual coaching strategies to create happy, healthy and social canine companions</p>
  </div>
  <div class="emblem" style="left:328px;top:38px;">
    <svg width="260" height="260" viewBox="0 0 260 260">
      <circle cx="130" cy="130" r="130" fill="var(--emblem-red)"/>
      <text x="130" y="137" text-anchor="middle" font-family="Arimo, Arial, sans-serif" font-size="26" font-weight="700" fill="#ffffff">Jolly Paws</text>
    </svg>
  </div>
  <div class="band-red"><span class="motto">Promoting communication and connection between dogs and their families</span></div>
</section>

<section class="card card--back" aria-label="Card back">
  <h1 class="person-name">Denise Carvell</h1>
  <p class="qualifications">Qualified in Dog Behavioural Training,<br>Natural Animal Healthcare &amp; Animal Health Science</p>
  <div class="band-red"></div>
  <div class="contact">
    <div class="contact-row">
      <svg width="11" height="16" viewBox="0 0 11 16"><rect x="1" y="1" width="9" height="14" rx="1.5" fill="none" stroke="#fff" stroke-width="1.6"/><rect x="3" y="3" width="5" height="5" fill="#fff"/></svg>
      <span>0400 126 358</span><span class="gap"></span>
      <svg width="16" height="11" viewBox="0 0 16 11"><rect width="16" height="11" fill="#fff"/><path d="M0 0 L8 6 L16 0" fill="none" stroke="#8a1a1c" stroke-width="1.4"/></svg>
      <span>jollypaws1@example.com</span>
    </div>
  </div>
  <div class="band-blue"></div>
  <div class="services">
    <h2>SERVICES</h2>
    <p>Providing individual coaching strategies to create happy, healthy and social canine companions</p>
  </div>
  <div class="emblem" style="left:382px;top:106px;">
    <svg width="216" height="216" viewBox="0 0 216 216">
      <circle cx="108" cy="108" r="108" fill="var(--emblem-red)"/>
      <text x="108" y="115" text-anchor="middle" font-family="Arimo, Arial, sans-serif" font-size="22" font-weight="700" fill="#ffffff">Jolly Paws</text>
    </svg>
  </div>
  <p class="footer-motto">Promoting communication and connection between dogs and their families</p>
</section>

</body>
</html>
```